Business Card Design (NEW FILES)

ATTENTION: New vector files are available. Please update your design to reflect/use the new (better resolution) logo images.

Seeking a unique and professional business card design for a commercial drone photography/videography business. The layout should feature
the logo (attached) and include the following information:
Owen Tarrick
614-502-7738
www.skylarkreelworks.example
NRD Certified Remote Pilot

Owen Tarrick

```html
<!DOCTYPE html>
<html lang="en">
<head>
<meta charset="utf-8">
<title>Skylark Reelworks – Business Card</title>
<link rel="stylesheet" href="https://fonts.googleapis.com/css2?family=Open+Sans:wght@400;600;700;800&display=swap">
<style>
  :root {
    --page: #1c1d21;
    --navy: #141a4a;
    --navy-emboss: #1d2668;
    --orange: #f08a3e;
    --white: #ffffff;
    --text-font: "Open Sans", Arial, sans-serif;
  }
  * { box-sizing: border-box; margin: 0; padding: 0; }
  html, body {
    width: 1200px; height: 780px; overflow: hidden;
    background: var(--page);
    font-family: var(--text-font);
  }
  .sheet {
    width: 1200px; height: 780px;
    display: flex; align-items: center; justify-content: center;
    gap: 40px;
  }
  .card {
    position: relative;
    width: 560px; height: 320px;
    background: var(--navy);
    border-radius: 18px;
    border: 3px solid var(--orange);
    overflow: hidden;
  }
  /* back side */
  .card--back .brand {
    position: absolute; inset: 0;
    display: flex; align-items: center; justify-content: center; gap: 14px;
  }
  .brand__name {
    font-family: var(--text-font);
    font-weight: 600;
    letter-spacing: 1px;
  }
  .card--back .brand__name { color: var(--navy-emboss); font-size: 38px; }
  .brand__dot { border-radius: 50%; flex: none; }
  .card--back .brand__dot { width: 30px; height: 30px; background: var(--navy-emboss); }

  /* front side */
  .card--front .brand {
    position: absolute; left: 34px; top: 62px;
    display: flex; align-items: center; gap: 10px;
  }
  .card--front .brand__name { color: var(--white); font-size: 27px; }
  .card--front .brand__dot { width: 22px; height: 22px; background: var(--orange); }

  .holder {
    position: absolute; right: 38px; top: 34px; text-align: right;
  }
  .holder__name { font-size: 27px; font-weight: 800; line-height: 1.1; }
  .holder__first { color: var(--orange); }
  .holder__last { color: var(--white); }
  .holder__role { color: var(--white); font-size: 14px; font-weight: 600; margin-top: 2px; }
  .holder__bar {
    position: absolute; right: 0; top: 34px;
    width: 20px; height: 52px; background: var(--orange);
  }

  .credentials {
    position: absolute; left: 72px; top: 168px;
    color: var(--white); font-size: 16px; font-weight: 600; line-height: 1.3;
  }
  .contacts {
    position: absolute; left: 40px; top: 222px;
    list-style: none; color: var(--white); font-size: 15px; font-weight: 600;
  }
  .contacts li { display: flex; align-items: center; gap: 12px; height: 26px; }
  .contacts svg { width: 16px; height: 16px; flex: none; }
</style>
</head>
<body>
<main class="sheet">
  <section class="card card--back" aria-label="Card back">
    <div class="brand">
      <span class="brand__dot"></span>
      <span class="brand__name">SKYLARK REELWORKS</span>
    </div>
  </section>

  <section class="card card--front" aria-label="Card front">
    <div class="brand">
      <span class="brand__dot"></span>
      <span class="brand__name">SKYLARK REELWORKS</span>
    </div>

    <span class="holder__bar"></span>
    <div class="holder">
      <p class="holder__name"><span class="holder__first">Owen</span> <span class="holder__last">Tarrick</span></p>
      <p class="holder__role">Owner</p>
    </div>

    <p class="credentials">NRD Certified Remote Pilot<br>Fully Insured</p>

    <ul class="contacts">
      <li>
        <svg viewBox="0 0 16 16" aria-hidden="true"><path fill="none" stroke="#f08a3e" stroke-width="2" stroke-linecap="round" d="M4 2 L6 5 L5 7 Q7 10 9 11 L11 10 L14 12 L12 14 Q5 13 2 4 Z"/></svg>
        614-502-7738
      </li>
      <li>
        <svg viewBox="0 0 16 16" aria-hidden="true"><circle cx="8" cy="8" r="6.5" fill="none" stroke="#f08a3e" stroke-width="1.6"/><ellipse cx="8" cy="8" rx="2.8" ry="6.5" fill="none" stroke="#f08a3e" stroke-width="1.3"/><path d="M1.5 8 H14.5" stroke="#f08a3e" stroke-width="1.3"/></svg>
        www.skylarkreelworks.example
      </li>
      <li>
        <svg viewBox="0 0 16 16" aria-hidden="true"><rect x="1.5" y="3.5" width="13" height="9" rx="1" fill="none" stroke="#f08a3e" stroke-width="1.6"/><path d="M2 4 L8 9 L14 4" fill="none" stroke="#f08a3e" stroke-width="1.6"/></svg>
        info@skylarkreelworks.example
      </li>
    </ul>
  </section>
</main>
</body>
</html>
```